wardrobe/costume stylist needs good business card for own business

Hi:)

I'm wanting a business card for my company. I am a freelance stylist.

I do wardrobe/costume stylist to TV commercials; Films; Fashion and Lifestyle shoots.

I'd like a design based around my name Rosalind Parfrey written nicely, maybe a colour? Up to you?!

I've attached a couple of images of business cards I like
.... be creative and have fun!

Thank you :)

Reason: I was trying to get my new business card ready for before I headed overseas Friday morning but I don't think that was realistic so I'd like to extend the deadline to give time to the project. Thank you

Hi designers:) Thank you for all your designs, I've extended the deadline until Sunday, so there's a bit more time. I've attached 3 pictures of business cards which I quite like, please take a look to see if it can be of help in your process. I like the pale plain or patterned background with dark font and the dark plain or patterned background with the pale font the motifs the feminine fonts the plain fonts I like the idea of playing with a circle or some shape on one side of the card with my name or initials as in the picture I have on my post could you play around with this idea a bit please? Thank you all for the work you've done :) Rosa

Hi I am working overseas til Saturday night sorry for no feedback until I teturn Thanks :) Rosa

Hi designers, Thank you all so much for submitting your designs, I really appreciate your input into my project :) I'm sorry I didn't get to respond to some comments, and give feedback. I didn't back from being away until later than I expected, and the deadline had passed then, so apologies. Thanks to you all again for all your really good designs :) Rosa

Target Market(s)

I am a freelance stylist my target audience is producers, production companies, photographers, directors...

Industry/Entity Type

Business

Requirements
Must have
• Rosalind Parfrey
Stylist or Wardrobe Stylist

email rosaparfrey@mailbox-example.co.nz
Mobile 0218467193

(Don't have to use the words 'email' and 'mobile')
Nice to have
• Would like it to be double sided
Like B & W
Like pale colour background with dark font or white font
Like dark colour background with pale font
Should not have
• I would prefer it not to incorporate pictures

```html
<!DOCTYPE html>
<html lang="en">
<head>
<meta charset="utf-8">
<title>Rosalind Parfrey – Stylist business card</title>
<link rel="stylesheet" href="https://fonts.googleapis.com/css2?family=Encode+Sans+Condensed:wght@300&display=swap">
<style>
  :root {
    --page: #ffffff;
    --card: #bdbda5;
    --ink: #6b6b69;
    --rule: #d3d3bf;
    --type: "Encode Sans Condensed", "Arial Narrow", sans-serif;
  }
  html, body {
    margin: 0;
    padding: 0;
    width: 1000px;
    height: 1200px;
    overflow: hidden;
    background: var(--page);
  }
  .sheet {
    position: relative;
    width: 1000px;
    height: 1200px;
    font-family: var(--type);
    font-weight: 300;
    color: var(--ink);
  }
  .card {
    position: absolute;
    left: 22px;
    width: 956px;
    height: 545px;
    background: var(--card);
  }
  .card--front { top: 43px; }
  .card--back { top: 612px; }

  .identity {
    position: absolute;
    right: 507px;
    top: 232px;
    text-align: center;
  }
  .identity__name {
    margin: 0;
    font-size: 56px;
    font-weight: 300;
    line-height: 1;
    letter-spacing: -0.5px;
  }
  .identity__role {
    margin: 8px 0 0;
    font-size: 31px;
    line-height: 1;
  }

  .divider {
    position: absolute;
    left: 487px;
    top: 57px;
    width: 3px;
    height: 403px;
    background: var(--rule);
  }

  .contact {
    position: absolute;
    left: 525px;
    top: 206px;
    margin: 0;
    padding: 0;
    list-style: none;
  }
  .contact__item {
    font-size: 27px;
    line-height: 1;
    letter-spacing: 0.3px;
  }
  .contact__item + .contact__item {
    margin-top: 22px;
    font-size: 33px;
  }

  .wordmark {
    position: absolute;
    left: 0;
    right: 0;
    top: 246px;
    margin: 0;
    text-align: center;
    font-size: 44px;
    font-weight: 300;
    line-height: 1;
  }
</style>
</head>
<body>
  <main class="sheet">
    <section class="card card--front" aria-label="Card front">
      <div class="identity">
        <h1 class="identity__name">Rosalind Parfrey</h1>
        <p class="identity__role">Stylist</p>
      </div>
      <div class="divider"></div>
      <ul class="contact">
        <li class="contact__item">rosaparfrey@mailbox-example.co.nz</li>
        <li class="contact__item">0218467193</li>
      </ul>
    </section>

    <section class="card card--back" aria-label="Card back">
      <p class="wordmark">Rosalind Parfrey</p>
    </section>
  </main>
</body>
</html>
```